Brellwick Partners, LLC Stationary

Brellwick Partners, LLC is a new financial planning and consulting company. We are looking for designs on business cards, letterhead, envelopes, and anything else that would be useful. Our preference for business card design is two sided. We are looking for a professional and clean look with incorporating the logo and patriotic feel. Thank you to all who participate and good luck!

```html
<!DOCTYPE html>
<html lang="en">
<head>
<meta charset="utf-8">
<title>Brellwick Partners, LLC – Business Card</title>
<link rel="stylesheet" href="https://fonts.googleapis.com/css2?family=Michroma&family=Open+Sans:wght@400;600&display=swap">
<style>
  :root {
    --page-bg: #dedad4;
    --card-bg: #f2f3f4;
    --navy: #1d2c4a;
    --red: #a3212a;
    --ink: #1f2430;
  }
  html, body {
    margin: 0;
    padding: 0;
    width: 1200px;
    height: 969px;
    overflow: hidden;
    background: var(--page-bg);
  }
  .card {
    position: absolute;
    left: 100px;
    top: 200px;
    width: 1000px;
    height: 570px;
    background: var(--card-bg);
    box-shadow: 0 10px 30px rgba(0,0,0,0.18);
    overflow: hidden;
    font-family: "Open Sans", Arial, sans-serif;
    color: var(--ink);
  }
  .accent-band {
    position: absolute;
    left: 0;
    top: 0;
    width: 1000px;
    height: 570px;
  }
  .company {
    position: absolute;
    right: 45px;
    top: 38px;
    margin: 0;
    text-align: right;
    font-family: "Michroma", "Arial Black", sans-serif;
    font-weight: 400;
    font-size: 40px;
    line-height: 50px;
    color: var(--navy);
    text-transform: uppercase;
  }
  .tagline {
    position: absolute;
    right: 45px;
    top: 146px;
    margin: 0;
    font-family: "Open Sans", Arial, sans-serif;
    font-weight: 600;
    font-size: 14px;
    letter-spacing: 2px;
    color: var(--ink);
    text-transform: uppercase;
  }
  .person-name {
    position: absolute;
    right: 45px;
    top: 213px;
    margin: 0;
    font-family: "Michroma", "Arial Black", sans-serif;
    font-size: 28px;
    color: var(--navy);
    text-transform: uppercase;
  }
  .person-title {
    position: absolute;
    right: 45px;
    top: 256px;
    margin: 0;
    font-family: "Open Sans", Arial, sans-serif;
    font-size: 27px;
    color: var(--red);
    font-variant: small-caps;
    letter-spacing: 1px;
  }
  .contact-list {
    position: absolute;
    right: 45px;
    top: 308px;
    margin: 0;
    padding: 0;
    list-style: none;
  }
  .contact-item {
    display: flex;
    justify-content: flex-end;
    align-items: center;
    gap: 12px;
    height: 38.5px;
    font-size: 23px;
  }
  .contact-icon {
    width: 22px;
    height: 22px;
    fill: var(--ink);
  }
  .address {
    position: absolute;
    right: 45px;
    top: 464px;
    margin: 0;
    text-align: right;
    font-style: normal;
    font-size: 23px;
    line-height: 39px;
  }
</style>
</head>
<body>
  <main class="card">
    <svg class="accent-band" viewBox="0 0 1000 570" aria-hidden="true">
      <polygon points="0,0 310,0 516,570 0,570" fill="var(--red)"/>
    </svg>

    <h1 class="company">Brellwick<br>Partners, LLC</h1>
    <p class="tagline">Financial Planning and Consulting</p>

    <h2 class="person-name">Dana Whitlock</h2>
    <p class="person-title">CEO/Founder</p>

    <ul class="contact-list">
      <li class="contact-item">
        <span>555 214 3870</span>
        <svg class="contact-icon" viewBox="0 0 24 24" aria-label="Phone"><path d="M6.6 10.8a15.1 15.1 0 0 0 6.6 6.6l2.2-2.2a1 1 0 0 1 1-.25 11.4 11.4 0 0 0 3.6.57 1 1 0 0 1 1 1V20a1 1 0 0 1-1 1A17 17 0 0 1 3 4a1 1 0 0 1 1-1h3.5a1 1 0 0 1 1 1c0 1.25.2 2.45.57 3.57a1 1 0 0 1-.25 1z"/></svg>
      </li>
      <li class="contact-item">
        <span>555 214 3871</span>
        <svg class="contact-icon" viewBox="0 0 24 24" aria-label="Fax"><path d="M7 3h10v5H7zM4 9h16a2 2 0 0 1 2 2v6h-4v4H6v-4H2v-6a2 2 0 0 1 2-2zm4 6v4h8v-4z"/></svg>
      </li>
      <li class="contact-item">
        <span>dana@brellwick.com</span>
        <svg class="contact-icon" viewBox="0 0 24 24" aria-label="Email"><path d="M3 5h18v14H3zm2 2v.4l7 4.6 7-4.6V7zm0 2.8V17h14V9.8l-7 4.6z"/></svg>
      </li>
      <li class="contact-item">
        <span>www.brellwick.com</span>
        <svg class="contact-icon" viewBox="0 0 24 24" aria-label="Website"><path d="M12 2a10 10 0 1 0 0 20 10 10 0 0 0 0-20zm-1 17.9A8 8 0 0 1 4.1 11H7a14 14 0 0 0 4 8.9zM13 4.1A8 8 0 0 1 19.9 11H17a14 14 0 0 0-4-6.9zM9 11a12 12 0 0 1 3-6.5A12 12 0 0 1 15 11zm3 8.5A12 12 0 0 1 9 13h6a12 12 0 0 1-3 6.5z"/></svg>
      </li>
    </ul>

    <address class="address">412 Harrow Street<br>Fairhollow, Alaska 99512</address>
  </main>
</body>
</html>
```